Velundra Jobs portal

Velundra Jobs is a job portal connecting job seekers and companies offering part time jobs in the Mena region, starting in the UAE. We would like to see designs that use the color blue. We have attached images to give an idea what the website should look like. When a company posts a job the job seekers are not allowed to see which company has posted a job. There should also be a coinvex gateway. On the landing page we want a catching picture that we will send.

Target Market(s)

Students and promotional workers

Logo Text

Velundra Jobs

Coding

Coded - Design and coding required

Number of Pages Required

4 page

Font styles to use
Sans Serif

Colors
33a6d7
0692cd
85cae6

```html
<!DOCTYPE html>
<html lang="en">
<head>
<meta charset="utf-8">
<title>Velundra Jobs</title>
<link rel="stylesheet" href="https://fonts.googleapis.com/css2?family=Open+Sans:wght@400;600;700;800&display=swap">
<style>
  :root {
    --blue-deep: #0692cd;
    --blue-mid: #33a6d7;
    --blue-light: #85cae6;
    --accent-text: #0a7fb6;
    --teal: #2fb3b8;
    --white: #ffffff;
    --sky-top: #8ccbe8;
    --sky-mid: #b9dcec;
    --haze: #d9e3e6;
    --city: #a7b4bd;
    --ground: #9c9a86;
  }
  * { box-sizing: border-box; margin: 0; padding: 0; }
  html, body { width: 1200px; height: 682px; overflow: hidden; }
  body { font-family: "Open Sans", Arial, sans-serif; color: var(--white); background: var(--sky-mid); }

  .landing { position: relative; width: 1200px; height: 682px; overflow: hidden; }

  .hero-backdrop {
    position: absolute; inset: 0 0 48px 0;
    background: linear-gradient(180deg, var(--sky-top) 0%, var(--sky-mid) 45%, var(--haze) 72%, var(--city) 88%, var(--ground) 100%);
  }
  .top-rule { position: absolute; left: 0; top: 0; width: 1200px; height: 3px; background: var(--blue-light); }

  .brand {
    position: absolute; left: 99px; top: 3px; width: 118px; height: 135px;
    background: var(--white); box-shadow: 0 2px 6px rgba(0,0,0,.18);
    display: flex; flex-direction: column; align-items: center;
  }
  .brand-mascot {
    width: 70px; height: 82px; margin-top: 8px; border-radius: 10px;
    background: linear-gradient(160deg, #7fcbe0 0%, #5a6fc0 55%, #d8529a 100%);
    opacity: .55;
  }
  .brand-name { margin-top: 6px; font-size: 21px; font-weight: 400; color: var(--teal); line-height: 1; }

  .account-nav { position: absolute; top: 3px; left: 860px; display: flex; gap: 13px; }
  .account-btn {
    display: flex; align-items: center; gap: 9px; height: 35px; width: 115px;
    padding-left: 11px; border-radius: 0 0 3px 3px; white-space: nowrap;
    font-size: 12px; font-weight: 600; letter-spacing: .2px; color: var(--white);
  }
  .account-btn--employer { background: linear-gradient(180deg, #9dc9dc, #79b2ca); }
  .account-btn--seeker { background: linear-gradient(180deg, var(--blue-mid), var(--blue-deep)); }

  .hero-title {
    position: absolute; left: 99px; top: 232px;
    font-size: 36px; font-weight: 800; line-height: 43px; letter-spacing: -.4px;
    white-space: nowrap;
  }
  .hero-title .highlight { color: var(--accent-text); }
  .hero-lead {
    position: absolute; left: 99px; top: 341px;
    font-size: 15px; line-height: 26px; font-weight: 400; white-space: nowrap;
  }

  .hero-actions { position: absolute; left: 99px; top: 420px; height: 44px; display: flex; align-items: center; }
  .join-btn {
    display: flex; align-items: center; gap: 10px; width: 134px; height: 44px; padding-left: 11px;
    background: linear-gradient(180deg, var(--blue-mid), var(--blue-deep));
    border: 1px solid #0a7fb6; border-radius: 3px; white-space: nowrap;
    font-size: 11.5px; font-weight: 600; color: var(--white);
  }
  .signin-note { margin-left: 14px; font-size: 15px; white-space: nowrap; }
  .signin-note .link { color: var(--accent-text); }
  .signin-mascot { margin-left: 14px; width: 26px; height: 36px; border-radius: 6px; background: linear-gradient(160deg, #7fcbe0, #5a6fc0 60%, #d8529a); opacity: .5; }

  .hero-portrait {
    position: absolute; left: 765px; top: 130px; width: 336px; height: 504px;
    border-radius: 140px 140px 0 0;
    background: linear-gradient(180deg, #c9ad85 0%, #d8b9a2 22%, #c8b29b 38%, #6b6f7d 55%, #575c6a 100%);
    opacity: .85;
  }

  .site-footer {
    position: absolute; left: 0; bottom: 0; width: 1200px; height: 48px;
    background: var(--blue-deep); display: flex; align-items: center;
    font-size: 13px; white-space: nowrap;
  }
  .copyright { position: absolute; left: 98px; }
  .social-list { position: absolute; left: 514px; display: flex; gap: 30px; list-style: none; }
  .social-list li { width: 11px; height: 11px; border-radius: 50%; background: var(--white); }
  .footer-links { position: absolute; right: 99px; display: flex; gap: 6px; list-style: none; }
</style>
</head>
<body>
<main class="landing">
  <div class="hero-backdrop" role="img" aria-label="Photograph of the Dubai skyline under a pale blue sky"></div>
  <div class="top-rule"></div>

  <a class="brand" aria-label="Velundra home">
    <div class="brand-mascot" role="img" aria-label="Brand mascot illustration"></div>
    <span class="brand-name">velundra</span>
  </a>

  <nav class="account-nav">
    <a class="account-btn account-btn--employer">
      <svg width="13" height="14" viewBox="0 0 13 14" aria-hidden="true"><circle cx="6.5" cy="3.6" r="3.3" fill="#fff"/><path d="M0 14c0-4 2.5-6 6.5-6s6.5 2 6.5 6z" fill="#fff"/></svg>
      EMPLOYER
    </a>
    <a class="account-btn account-btn--seeker">
      <svg width="18" height="14" viewBox="0 0 18 14" aria-hidden="true"><circle cx="9" cy="3.5" r="3" fill="#fff"/><circle cx="3.5" cy="4.5" r="2.3" fill="#fff"/><circle cx="14.5" cy="4.5" r="2.3" fill="#fff"/><path d="M4 14c0-3.5 2-5.5 5-5.5s5 2 5 5.5z M0 12c0-2.5 1.3-4 3.5-4 1 0 1.8.3 2.3.8C4.6 9.7 4 11 4 12z M18 12c0-2.5-1.3-4-3.5-4-1 0-1.8.3-2.3.8 1.2.9 1.8 2.2 1.8 3.2z" fill="#fff"/></svg>
      JOB SEEKER
    </a>
  </nav>

  <h1 class="hero-title">Number one platform connecting<br>people with <span class="highlight">events companies.</span></h1>
  <p class="hero-lead">We are &nbsp;Providing part time job for students in Dubai, if you are a student and have quite<br>free time and want to invest it gaining extra money, so you are in the right place .</p>

  <div class="hero-actions">
    <a class="join-btn">
      <svg width="16" height="15" viewBox="0 0 16 15" aria-hidden="true"><path d="M16 0 0 7l4.5 1.6L13 2.5 6 9.5V15l2.7-3.6L12.5 13z" fill="#fff"/></svg>
      JOIN VELUNDRA
    </a>
    <span class="signin-note">for our users you can <a class="link">sign in !</a></span>
    <div class="signin-mascot" role="img" aria-label="Small mascot illustration"></div>
  </div>

  <div class="hero-portrait" role="img" aria-label="Photograph of a smiling businesswoman in a grey blazer with arms crossed"></div>

  <footer class="site-footer">
    <span class="copyright">Copyrights are reserved to Velundra 2015</span>
    <ul class="social-list" aria-label="Social networks">
      <li></li><li></li><li></li><li></li><li></li>
    </ul>
    <ul class="footer-links">
      <li>About us</li><li>-</li><li>terms and conditions</li><li>-</li><li>Sitemap</li>
    </ul>
  </footer>
</main>
</body>
</html>
```